Business card design needed

I run a Beautician studio (for 7 years now)
I offer
- Velmo Body Sugaring
- Ruby Glaze
- Nails
- Facials
- Manicure
- Foot Treatment
It might not be necessary to list all those treatments?
Maybe the link to the Website is sufficient?
I leave that up to you ...
(more info on www.FernAndDewByLenka.com.au)
Velmo BodySugaring is our biggest success, It replaces waxing.
I would like to incorporate the logo into the Business Card.
We had many complaints regarding our old Business Cards as the Phone Number was to small.
On the backside, we would like a "your next Appointment" section.
Looking forward to you Design, cheers ... Lenka
Industry/Entity Type
Business
Contact Information for Business Card
Fern by Dew by Lenka
14 Korrin Sqr 3942 Dunmoor
www.FernAndDewByLenka.com.au
03 9481 2267

```html
<!DOCTYPE html>
<html lang="en">
<head>
<meta charset="utf-8">
<title>Fern &amp; Dew by Lenka – Business Card</title>
<link rel="stylesheet" href="https://fonts.googleapis.com/css2?family=Ubuntu:ital,wght@0,400;0,500;1,500;1,700&family=PT+Sans:ital,wght@0,400;0,700;1,700&family=Tinos&display=swap">
<style>
  :root {
    --backdrop: #e9e6e2;
    --card: #ffffff;
    --ink: #3a3a3a;
    --ink-soft: #555555;
    --band-dark: #58595b;
    --band-light: #bcbdbf;
    --accent: #f0a22b;
    --faint-accent: rgba(240, 162, 43, 0.10);
  }
  * { box-sizing: border-box; margin: 0; padding: 0; }
  html, body { width: 1200px; height: 788px; overflow: hidden; }
  body {
    background: var(--backdrop);
    position: relative;
    font-family: "PT Sans", Arial, sans-serif;
    color: var(--ink);
  }
  .side-label {
    position: absolute;
    font-size: 21px;
    color: #222;
    transform: translateX(-50%);
  }
  .card {
    position: absolute;
    width: 524px;
    height: 300px;
    background: var(--card);
    border-radius: 22px;
    overflow: hidden;
    box-shadow: 0 3px 8px rgba(0,0,0,.25);
  }
  .card > * { position: absolute; }

  /* Brand */
  .studio-name {
    font-family: "Ubuntu", Arial, sans-serif;
    font-weight: 400;
    letter-spacing: 1px;
    color: var(--ink);
    white-space: nowrap;
  }
  .partner-mark { display: flex; align-items: center; gap: 8px; }
  .partner-mark .dot { width: 28px; height: 28px; border-radius: 50%; background: var(--accent); }
  .partner-mark .name {
    font-family: "Ubuntu", Arial, sans-serif;
    font-size: 22px; letter-spacing: 3px; color: var(--ink);
  }

  /* Front */
  .front { left: 338px; top: 74px; }
  .front .swoosh { left: 0; top: 0; width: 524px; height: 300px; }
  .front .studio-name { left: 22px; top: 38px; font-size: 34px; }
  .front .partner-mark { left: 24px; top: 120px; }
  .contact { left: 22px; top: 198px; font-size: 17px; line-height: 26px; color: var(--ink); }
  .contact b { font-style: italic; font-weight: 700; margin-right: 2px; }

  /* Back 1 */
  .back-one { left: 54px; top: 443px; }
  .back-one .studio-name { left: 0; width: 524px; text-align: center; top: 12px; font-size: 25px; }
  .back-one .header-rule { left: 0; top: 50px; width: 524px; height: 1px; background: var(--ink-soft); }
  .faint-disc {
    left: 165px; top: 118px; width: 200px; height: 200px;
    border-radius: 50%; background: var(--faint-accent);
  }
  .col-title { font-style: italic; font-weight: 700; font-size: 18px; color: #2d2d2d; }
  .offer-title { left: 29px; top: 70px; }
  .service-list { left: 30px; top: 97px; list-style: none; font-family: "Tinos", "Times New Roman", serif; font-size: 14.5px; color: #5c5c5c; line-height: 20px; }
  .service-list li::before { content: "\25AA"; font-size: 10px; margin-right: 6px; vertical-align: 2px; }
  .column-rule { left: 206px; top: 72px; width: 2px; height: 146px; background: #7a7a7a; }
  .appt-title { left: 243px; top: 70px; }
  .appt-field { left: 243px; font-size: 17px; color: #333; display: flex; align-items: flex-end; }
  .appt-field .blank { display: inline-block; border-bottom: 1px solid #333; height: 16px; }
  .hours-small { left: 0; width: 524px; text-align: center; }
  .hours-small.title { top: 238px; font-style: italic; font-weight: 700; font-size: 15px; }
  .hours-small.times { top: 261px; font-size: 13px; word-spacing: 1px; }

  /* Back 2 */
  .back-two { left: 621px; top: 443px; }
  .hours-title { left: 33px; top: 29px; font-style: italic; font-weight: 700; font-size: 20px; letter-spacing: 1px; color: #333; }
  .hours-list { left: 30px; top: 61px; font-size: 18px; line-height: 24px; color: #222; }
  .back-two .partner-mark { left: 388px; top: 58px; }
  .back-two .divider { left: 29px; top: 117px; width: 466px; height: 1px; background: #bdbdbd; }
  .form-line { font-size: 18px; color: #333; display: flex; align-items: flex-end; white-space: nowrap; }
  .form-line .blank { display: inline-block; border-bottom: 1px solid #333; height: 18px; }
  .name-line { left: 46px; top: 145px; }
  .date-line { left: 35px; top: 195px; }
  .day-boxes { left: 60px; top: 249px; display: flex; gap: 16px; font-size: 18px; color: #333; }
  .day-boxes span { display: flex; align-items: center; gap: 10px; }
  .day-boxes span::before { content: ""; width: 22px; height: 22px; border: 1px solid #333; display: inline-block; }
</style>
</head>
<body>
  <div class="side-label" style="left:600px; top:34px;">Front</div>
  <div class="side-label" style="left:323px; top:403px;">Back - 1</div>
  <div class="side-label" style="left:897px; top:403px;">Back - 2</div>

  <section class="card front">
    <svg class="swoosh" viewBox="0 0 524 300" aria-hidden="true">
      <path d="M288,300 C380,262 470,205 490,118 C498,190 470,255 436,300 Z" fill="var(--band-light)"/>
      <path d="M420,0 L524,0 L524,300 L414,300 C455,240 492,170 487,110 C482,60 455,22 420,0 Z" fill="var(--band-dark)" stroke="#fff" stroke-width="5"/>
    </svg>
    <h1 class="studio-name">FERN&amp;DEW BY LENKA</h1>
    <div class="partner-mark"><span class="dot"></span><span class="name">VELMO</span></div>
    <div class="contact">
      <div><b>ph</b> 03 9481 2267</div>
      <div><b>a</b> 14 Korrin Sqr, 3942 Dunmoor</div>
      <div><b>w</b> www.FernAndDewByLenka.com.au</div>
    </div>
  </section>

  <section class="card back-one">
    <div class="faint-disc" aria-hidden="true"></div>
    <h2 class="studio-name">FERN&amp;DEW BY LENKA</h2>
    <div class="header-rule"></div>
    <div class="col-title offer-title">I offer</div>
    <ul class="service-list">
      <li>Velmo Body Sugaring</li>
      <li>Ruby Glaze</li>
      <li>Nails</li>
      <li>Facials</li>
      <li>Manicure</li>
      <li>Foot Treatment</li>
    </ul>
    <div class="column-rule"></div>
    <div class="col-title appt-title">An Appointment</div>
    <div class="appt-field" style="top:111px;">Name<span class="blank" style="width:217px;"></span></div>
    <div class="appt-field" style="top:151px;">Date<span class="blank" style="width:226px;"></span></div>
    <div class="appt-field" style="top:191px;">time<span class="blank" style="width:160px;"></span>&nbsp;am / pm</div>
    <div class="hours-small title">Hours of Operation</div>
    <div class="hours-small times">Mon. to Fri.&nbsp; 7.30am - 7.00pm&nbsp;&nbsp;&nbsp;&nbsp;&nbsp;&nbsp;&nbsp;&nbsp;&nbsp;Sat. 7.30am - 12.00pm</div>
  </section>

  <section class="card back-two">
    <h2 class="hours-title">Hours of Operation</h2>
    <div class="hours-list">
      <div>Monday to Friday -&nbsp; 7.30am - 7.00pm</div>
      <div>Saturday - 7.30am - 12.00pm</div>
    </div>
    <div class="partner-mark"><span class="dot"></span><span class="name">VELMO</span></div>
    <div class="divider"></div>
    <div class="form-line name-line"><span class="blank" style="width:262px;"></span>&nbsp;has an appointment</div>
    <div class="form-line date-line">Date :<span class="blank" style="width:42px;"></span>&nbsp;/&nbsp;<span class="blank" style="width:42px;"></span>&nbsp;/&nbsp;<span class="blank" style="width:52px;"></span>&nbsp;&nbsp;@&nbsp;<span class="blank" style="width:42px;"></span>&nbsp;:&nbsp;<span class="blank" style="width:52px;"></span>am / pm</div>
    <div class="day-boxes">
      <span>Mon.</span><span>Tue.</span><span>Wed.</span><span>Thu.</span><span>Fri.</span>
    </div>
  </section>
</body>
</html>
```